Design a Mobile App for Landscape Businesses

This project is to design the first three screens for a mobile app for Landscape and Lawncare businesses. This app will serve as a directory for homeowners to locate landscape and lawn care businesses and for landscape businesses and contractors to run their business. See the attached PDF for more information and example
Here is the link to the description https://lnkbrev.example/q7z3Kp

Target Market(s)

Landscape and lawn care business, gardeners, home owners

Industry/Entity Type

Landscape Gardening

Logo Text

Verdalink

Colors

Designer to choose colors to be used in the design.

```html
<!DOCTYPE html>
<html lang="en">
<head>
<meta charset="utf-8">
<title>Verdalink – app screens</title>
<link href="https://fonts.googleapis.com/css2?family=Montserrat:wght@400;500;600;700&display=swap" rel="stylesheet">
<style>
:root{
  --green:#3aa935;
  --green-dark:#2f9430;
  --text:#222;
  --muted:#666;
  --line:#e3e6e8;
  --field-bg:#f1f3f4;
  --social-a:#2d6db5;
  --social-b:#22bcd8;
  --alert:#ff5a1f;
  --badge:#c9d3d6;
  --page:#ffffff;
}
*{box-sizing:border-box;margin:0;padding:0}
html,body{width:932px;height:1200px;overflow:hidden;background:var(--page);font-family:"Montserrat",sans-serif;color:var(--text)}
.screen{position:absolute;width:297px;background:#fff;overflow:hidden;box-shadow:0 1px 4px rgba(0,0,0,.15)}
.abs{position:absolute}
.status{position:absolute;top:0;left:0;right:0;height:18px;font-size:8px;font-weight:600;text-align:right;padding:5px 6px 0 0;z-index:5}
.topbar{position:absolute;top:18px;left:0;right:0;height:35px;border-bottom:1px solid var(--line);background:#fff}
.topbar h1{position:absolute;left:11px;top:10px;font-size:12px;font-weight:700}
.top-actions{position:absolute;right:11px;top:11px;font-size:10px;color:var(--green);font-weight:600;display:flex;gap:14px}
.top-actions span{display:flex;align-items:center;gap:3px}
.filters{position:absolute;left:0;right:0;height:34px;display:flex;background:#fff;font-size:9px}
.filters div{flex:1;display:flex;align-items:center;gap:5px;padding:0 8px;position:relative}
.filters div+div{border-left:1px solid var(--line)}
.filters .chev{position:absolute;right:8px}
.map{position:absolute;left:0;right:0;top:53px;bottom:37px;background:linear-gradient(150deg,#e8ece8 0%,#dfe8dc 35%,#cfe3f0 55%,#e9ebe9 75%,#d8e8cf 100%)}
.marker{position:absolute;background:var(--green);color:#fff;font-size:8px;font-weight:700;padding:4px 6px;border-radius:2px;border:2px solid #fff}
.marker::after{content:"";position:absolute;left:50%;bottom:-8px;width:2px;height:6px;background:#555}
.card{position:absolute;left:0;right:0;background:#fff}
.card h2{font-size:12px;font-weight:700;margin-bottom:8px}
.card p{font-size:8.6px;line-height:13px;color:#444;width:210px}
.quote{position:absolute;right:12px;font-size:9.5px;font-weight:600;color:var(--green);display:flex;align-items:center;gap:4px}
.phone{font-size:9.5px;display:flex;align-items:center;gap:4px;margin-top:8px}
.nav{position:absolute;left:0;right:0;height:37px;border-top:1px solid var(--line);background:#fff;display:flex}
.nav div{flex:1;text-align:center;font-size:7.5px;color:#999;padding-top:6px;position:relative}
.nav div.on{color:var(--green);font-weight:600}
.nav svg{display:block;margin:0 auto 3px}
.nav .dot{position:absolute;top:5px;left:calc(50% + 4px);width:6px;height:6px;border-radius:50%;background:var(--alert)}
.photo{position:absolute;left:0;right:0}
.tags{position:absolute;display:flex;gap:5px}
.tag{font-size:8px;border:1px solid;padding:4px 8px;display:flex;align-items:center;gap:3px}
.tag.dark{color:#fff;border-color:rgba(255,255,255,.8);background:rgba(0,0,0,.45)}
.tag.light{color:#333;border-color:var(--green)}
.section-title{font-size:9.5px;font-weight:700}
.services{position:absolute;left:0;right:0;display:flex;border-top:1px solid var(--line)}
.services div{flex:1;text-align:center;font-size:9.5px;color:#444;padding-top:16px;height:66px}
.services div+div{border-left:1px solid var(--line)}
.services svg{display:block;margin:0 auto 6px}
.btn{position:absolute;height:35px;display:flex;align-items:center;justify-content:center;gap:6px;color:#fff;font-size:10px;font-weight:700}
.btn.primary{background:var(--green)}
.btn.social-a{background:var(--social-a)}
.btn.social-b{background:var(--social-b)}
.sq{width:11px;height:11px;background:#fff;display:inline-block;border-radius:1px}
.ring{width:11px;height:11px;border:2px solid #fff;border-radius:50%;display:inline-block}
.form{background:#eef1f2}
.progress{position:absolute;left:0;right:0;top:56px;height:4px;background:#e2e5e6}
.progress i{display:block;height:100%;background:var(--green)}
.form h3{position:absolute;left:10px;top:84px;font-size:16px;font-weight:500;color:#333}
.label{position:absolute;font-size:8px;font-weight:600;color:#333;letter-spacing:.2px}
.field{position:absolute;height:36px;background:#fff;border:1px solid #dde1e3;font-size:9.5px;display:flex;align-items:center;padding:0 10px;color:#333}
.login-bg{position:absolute;inset:0;background:linear-gradient(180deg,#4b5d63 0%,#3f5a52 40%,#5f7f57 70%,#7a8f5c 100%)}
.login-input{position:absolute;left:13px;width:273px;height:36px;background:#fff;display:flex;align-items:center;gap:8px;padding:0 12px;font-size:10px;color:#333}
.profile-badge{position:absolute;left:220px;top:160px;width:66px;height:66px;border-radius:50%;background:#e9ecee;display:flex;align-items:center;justify-content:center}
.profile-badge i{width:40px;height:40px;border-radius:50%;background:var(--badge)}
</style>
</head>
<body>

<section class="screen" style="left:10px;top:11px;height:528px">
  <div class="status">⏰ ▾◢ ▯ 16:54</div>
  <div class="topbar">
    <h1>Find a Gardener</h1>
    <div class="top-actions">
      <span><svg width="9" height="9" viewBox="0 0 10 10"><path d="M1 1h8L6 5v4L4 8V5z" fill="none" stroke="currentColor" stroke-width="1.2"/></svg>Filter</span>
      <span><svg width="9" height="9" viewBox="0 0 10 10"><path d="M1 2h8M1 5h8M1 8h8" stroke="currentColor" stroke-width="1.2"/></svg>List</span>
    </div>
  </div>
  <div class="map" role="img" aria-label="Street map of the city centre with river, parks and landmarks"></div>
  <div class="marker" style="left:53px;top:138px">AG</div>
  <div class="marker" style="left:131px;top:231px;font-size:10px;padding:5px 9px">WL</div>
  <div class="marker" style="left:228px;top:262px">AB</div>
  <div class="marker" style="left:14px;top:329px">WG</div>
  <div class="filters" style="top:59px;left:6px;right:6px;box-shadow:0 1px 3px rgba(0,0,0,.2)">
    <div><svg width="8" height="10" viewBox="0 0 8 10"><path d="M4 10S0 5.5 0 3.8a4 4 0 0 1 8 0C8 5.5 4 10 4 10z" fill="var(--green)"/><circle cx="4" cy="3.8" r="1.4" fill="#fff"/></svg><b style="font-weight:600">Current Location</b><svg class="chev" width="8" height="5" viewBox="0 0 8 5"><path d="M1 1l3 3 3-3" fill="none" stroke="#333"/></svg></div>
    <div><svg width="10" height="10" viewBox="0 0 10 10"><circle cx="5" cy="5" r="4" fill="none" stroke="var(--green)" stroke-width="1.2"/><path d="M5 3v2.3l1.5 1" fill="none" stroke="var(--green)"/></svg>Available: <b style="font-weight:600">Anytime</b><svg class="chev" width="8" height="5" viewBox="0 0 8 5"><path d="M1 1l3 3 3-3" fill="none" stroke="#333"/></svg></div>
  </div>
  <div class="card" style="top:390px;height:101px;padding:19px 11px 0;border-radius:8px 8px 0 0;box-shadow:0 -1px 4px rgba(0,0,0,.12)">
    <i class="abs" style="left:137px;top:7px;width:30px;height:3px;background:#ddd;border-radius:2px"></i>
    <h2>Hartley’s Landscaping</h2>
    <p>Experienced and skilled gardener based in Scarborough. I specialise in law care, hedge…</p>
    <div class="quote" style="top:48px">Quote <svg width="6" height="10" viewBox="0 0 6 10"><path d="M1 1l4 4-4 4" fill="none" stroke="currentColor" stroke-width="1.3"/></svg></div>
    <div class="phone"><svg width="7" height="11" viewBox="0 0 7 11"><rect x=".6" y=".6" width="5.8" height="9.8" rx="1" fill="none" stroke="var(--green)" stroke-width="1.1"/></svg>07000 555 218</div>
  </div>
  <nav class="nav" style="top:491px">
    <div class="on"><svg width="14" height="12" viewBox="0 0 14 12"><path d="M4 11S0 6.5 0 4.3a4 4 0 0 1 8 0C8 6.5 4 11 4 11z" fill="var(--green)"/><circle cx="11" cy="8" r="2.5" fill="none" stroke="var(--green)" stroke-width="1.3"/></svg>Search</div>
    <div><svg width="12" height="11" viewBox="0 0 12 11"><path d="M0 1.5h2M4 1.5h8M0 5.5h2M4 5.5h8M0 9.5h2M4 9.5h8" stroke="#aaa"/></svg>Bookings</div>
    <div><svg width="14" height="11" viewBox="0 0 14 11"><rect x=".5" y="1.5" width="13" height="9" fill="none" stroke="#aaa"/><path d="M.5 1.5l6.5 5 6.5-5" fill="none" stroke="#aaa"/></svg><i class="dot"></i>Messages</div>
    <div><svg width="12" height="12" viewBox="0 0 12 12"><circle cx="6" cy="6" r="4.5" fill="none" stroke="#aaa" stroke-dasharray="2 1"/><circle cx="6" cy="6" r="2" fill="none" stroke="#aaa"/></svg>Account</div>
  </nav>
</section>

<section class="screen" style="left:318px;top:11px;height:528px">
  <div class="status">⏰ ▾◢ ▯ 16:54</div>
  <div class="topbar" style="border:none">
    <h1>Find a Gardener</h1>
    <div class="top-actions">
      <span><svg width="9" height="9" viewBox="0 0 10 10"><path d="M1 1h8L6 5v4L4 8V5z" fill="none" stroke="currentColor" stroke-width="1.2"/></svg>Filter</span>
      <span><svg width="10" height="9" viewBox="0 0 10 9"><path d="M.5 1.5l3-1 3 1 3-1v7l-3 1-3-1-3 1z M3.5.5v7M6.5 1.5v7" fill="none" stroke="currentColor"/></svg>Map</span>
    </div>
  </div>
  <div class="filters" style="top:53px;height:40px;border-top:1px solid var(--line);border-bottom:1px solid var(--line)">
    <div><svg width="8" height="10" viewBox="0 0 8 10"><path d="M4 10S0 5.5 0 3.8a4 4 0 0 1 8 0C8 5.5 4 10 4 10z" fill="var(--green)"/><circle cx="4" cy="3.8" r="1.4" fill="#fff"/></svg><b style="font-weight:600">Current Location</b><svg class="chev" width="8" height="5" viewBox="0 0 8 5"><path d="M1 1l3 3 3-3" fill="none" stroke="#333"/></svg></div>
    <div><svg width="10" height="10" viewBox="0 0 10 10"><circle cx="5" cy="5" r="4" fill="none" stroke="var(--green)" stroke-width="1.2"/><path d="M5 3v2.3l1.5 1" fill="none" stroke="var(--green)"/></svg>Available: <b style="font-weight:600">Anytime</b><svg class="chev" width="8" height="5" viewBox="0 0 8 5"><path d="M1 1l3 3 3-3" fill="none" stroke="#333"/></svg></div>
  </div>
  <div class="photo" style="top:98px;height:157px;background:linear-gradient(180deg,#9a8f86 0%,#7d5f52 35%,#4e6b3c 65%,#2f4a26 100%)" role="img" aria-label="Brick house with landscaped front garden and shrubs"></div>
  <div class="tags" style="left:9px;top:222px">
    <span class="tag dark">● Scarborough</span><span class="tag dark">● Whitby</span><span class="tag dark">● Filey</span>
  </div>
  <div class="card" style="top:255px;height:99px;padding:21px 12px 0">
    <h2>Hartley’s Landscaping</h2>
    <p>Experienced and skilled gardener based in Scarborough. I specialise in law care, hedge…</p>
    <div class="quote" style="top:50px">Quote <svg width="6" height="10" viewBox="0 0 6 10"><path d="M1 1l4 4-4 4" fill="none" stroke="currentColor" stroke-width="1.3"/></svg></div>
    <div class="phone"><svg width="7" height="11" viewBox="0 0 7 11"><rect x=".6" y=".6" width="5.8" height="9.8" rx="1" fill="none" stroke="var(--green)" stroke-width="1.1"/></svg>07000 555 218</div>
  </div>
  <div class="photo" style="top:354px;height:140px;background:linear-gradient(180deg,#4f7ec7 0%,#8fb0d8 30%,#5d5a4a 60%,#3e4a30 100%)" role="img" aria-label="Bungalow with trees and a pool in the garden"></div>
  <div class="tags" style="left:9px;top:477px">
    <span class="tag dark">● Scarborough</span><span class="tag dark">● Whitby</span><span class="tag dark">● Filey</span>
  </div>
  <nav class="nav" style="top:491px">
    <div class="on"><svg width="14" height="12" viewBox="0 0 14 12"><path d="M4 11S0 6.5 0 4.3a4 4 0 0 1 8 0C8 6.5 4 11 4 11z" fill="var(--green)"/><circle cx="11" cy="8" r="2.5" fill="none" stroke="var(--green)" stroke-width="1.3"/></svg>Search</div>
    <div><svg width="12" height="11" viewBox="0 0 12 11"><path d="M0 1.5h2M4 1.5h8M0 5.5h2M4 5.5h8M0 9.5h2M4 9.5h8" stroke="#aaa"/></svg>Bookings</div>
    <div><svg width="14" height="11" viewBox="0 0 14 11"><rect x=".5" y="1.5" width="13" height="9" fill="none" stroke="#aaa"/><path d="M.5 1.5l6.5 5 6.5-5" fill="none" stroke="#aaa"/></svg><i class="dot"></i>Messages</div>
    <div><svg width="12" height="12" viewBox="0 0 12 12"><circle cx="6" cy="6" r="4.5" fill="none" stroke="#aaa" stroke-dasharray="2 1"/><circle cx="6" cy="6" r="2" fill="none" stroke="#aaa"/></svg>Account</div>
  </nav>
</section>

<section class="screen" style="left:626px;top:11px;height:643px;background:#f0f2f3">
  <div class="photo" style="top:0;height:192px;background:linear-gradient(180deg,#5b6f7a 0%,#6d5548 35%,#4c6a34 65%,#3a5a28 100%)" role="img" aria-label="Front garden with trimmed shrubs and flower beds before a brick house"></div>
  <div class="status" style="color:#fff">⏰ ▾◢ ▯ 16:54</div>
  <svg class="abs" style="left:10px;top:26px" width="14" height="12" viewBox="0 0 14 12"><path d="M13 6H2M6 1L1 6l5 5" fill="none" stroke="#fff" stroke-width="1.6"/></svg>
  <div class="abs" style="left:30px;top:24px;color:#fff;font-size:12px;font-weight:700">Find a Gardener</div>
  <svg class="abs" style="right:10px;top:22px" width="16" height="16" viewBox="0 0 16 16"><path d="M8 1l2 4.6 5 .5-3.8 3.3 1.1 4.9L8 11.8 3.7 14.3l1.1-4.9L1 6.1l5-.5z" fill="none" stroke="#fff" stroke-width="1.2"/></svg>
  <div class="abs" style="left:131px;top:180px;display:flex;gap:4px">
    <i style="width:5px;height:5px;border-radius:50%;background:#fff"></i><i style="width:5px;height:5px;border-radius:50%;background:rgba(255,255,255,.6)"></i><i style="width:5px;height:5px;border-radius:50%;background:rgba(255,255,255,.6)"></i><i style="width:5px;height:5px;border-radius:50%;background:rgba(255,255,255,.6)"></i>
  </div>
  <div class="abs" style="left:0;right:0;top:192px;height:103px;background:#fff"></div>
  <div class="profile-badge" role="img" aria-label="Partner badge"><i></i></div>
  <div class="abs" style="left:10px;top:205px;font-size:14px;font-weight:700">Hartley’s Landscaping</div>
  <div class="abs" style="left:10px;top:232px;font-size:9.5px;display:flex;gap:12px;align-items:center">
    <span style="display:flex;gap:4px;align-items:center"><svg width="7" height="11" viewBox="0 0 7 11"><rect x=".6" y=".6" width="5.8" height="9.8" rx="1" fill="none" stroke="var(--green)" stroke-width="1.1"/></svg>07000 555 218</span>
    <span style="display:flex;gap:4px;align-items:center"><svg width="9" height="11" viewBox="0 0 9 11"><path d="M4.5 10.3S.6 6 .6 4.1a3.9 3.9 0 0 1 7.8 0C8.4 6 4.5 10.3 4.5 10.3z" fill="none" stroke="var(--green)" stroke-width="1.1"/><circle cx="4.5" cy="4" r="1.3" fill="none" stroke="var(--green)"/></svg>London, UK</span>
  </div>
  <div class="tags" style="left:12px;top:262px">
    <span class="tag light"><b style="color:var(--green)">●</b> Scarborough</span><span class="tag light"><b style="color:var(--green)">●</b> Whitby</span><span class="tag light"><b style="color:var(--green)">●</b> Filey</span>
  </div>
  <div class="abs" style="left:0;right:0;top:302px;height:124px;background:#fff;padding:14px 15px">
    <div class="section-title">Bio</div>
    <p style="font-size:9px;line-height:16px;color:#555;margin-top:9px">Experienced and skilled gardener based in Scarborough. I specialise in law care, hedge mae cenas sed diam eget risus varius blandit sit amet non magna. Fusce dapibus, tellus ac cursus commodo, tortor mauris.</p>
  </div>
  <div class="abs" style="left:0;right:0;top:432px;height:103px;background:#fff">
    <div class="section-title" style="padding:14px 15px">Services</div>
    <div class="services" style="top:38px">
      <div><svg width="12" height="12" viewBox="0 0 12 12"><path d="M6 11V4M3 11L1 5M9 11l2-6M4.5 11L4 2M7.5 11L8 2" stroke="var(--green)" fill="none"/></svg>Lawn Care</div>
      <div><svg width="12" height="12" viewBox="0 0 12 12"><path d="M1 11l4-4M5 7l2-2 2.5 2.5L11 1 6 3.5z" stroke="var(--green)" fill="none" stroke-width="1.3"/></svg>Landscaping</div>
      <div><svg width="12" height="13" viewBox="0 0 12 13"><path d="M6 1L3 5h2L2 9h3v3h2V9h3L7 5h2z" stroke="var(--green)" fill="none"/></svg>Landscaping</div>
    </div>
  </div>
  <div class="btn primary" style="left:8px;top:551px;width:280px">Get a Quote <svg width="6" height="9" viewBox="0 0 6 10"><path d="M1 1l4 4-4 4" fill="none" stroke="#fff" stroke-width="1.3"/></svg></div>
  <nav class="nav" style="top:606px">
    <div class="on"><svg width="14" height="12" viewBox="0 0 14 12"><path d="M4 11S0 6.5 0 4.3a4 4 0 0 1 8 0C8 6.5 4 11 4 11z" fill="var(--green)"/><circle cx="11" cy="8" r="2.5" fill="none" stroke="var(--green)" stroke-width="1.3"/></svg>Search</div>
    <div><svg width="12" height="11" viewBox="0 0 12 11"><path d="M0 1.5h2M4 1.5h8M0 5.5h2M4 5.5h8M0 9.5h2M4 9.5h8" stroke="#aaa"/></svg>Bookings</div>
    <div><svg width="14" height="11" viewBox="0 0 14 11"><rect x=".5" y="1.5" width="13" height="9" fill="none" stroke="#aaa"/><path d="M.5 1.5l6.5 5 6.5-5" fill="none" stroke="#aaa"/></svg><i class="dot"></i>Messages</div>
    <div><svg width="12" height="12" viewBox="0 0 12 12"><circle cx="6" cy="6" r="4.5" fill="none" stroke="#aaa" stroke-dasharray="2 1"/><circle cx="6" cy="6" r="2" fill="none" stroke="#aaa"/></svg>Account</div>
  </nav>
</section>

<section class="screen" style="left:10px;top:664px;height:528px">
  <div class="login-bg" role="img" aria-label="Gardener watering a flower bed, softly darkened"></div>
  <div class="status" style="color:#fff">⏰ ▾◢ ▯ 16:54</div>
  <i class="abs" style="left:136px;top:62px;width:26px;height:26px;border-radius:50%;border:2px solid #fff"></i>
  <div class="abs" style="left:0;right:0;top:106px;text-align:center;color:#fff;font-size:17px;font-weight:700">Verdalink</div>
  <div class="abs" style="left:0;right:0;top:130px;text-align:center;color:#fff;font-size:9px;letter-spacing:9px">LOGO TBC</div>
  <div class="abs" style="left:0;right:0;top:155px;text-align:center;color:#fff;font-size:12px;font-weight:500">On demand gardening services</div>
  <div class="abs" style="left:0;right:0;top:208px;text-align:center;color:#fff;font-size:9.5px">Already have an account? <b>Log in</b></div>
  <div class="btn social-a" style="left:9px;width:280px;top:257px"><i class="sq"></i>Sign up with Socialine</div>
  <div class="btn social-b" style="left:9px;width:280px;top:300px"><i class="ring"></i>Sign up with Chirper</div>
  <div class="login-input" style="top:375px"><svg width="12" height="9" viewBox="0 0 12 9"><rect x=".5" y=".5" width="11" height="8" fill="none" stroke="#4a90d9"/><path d="M.5.5l5.5 4 5.5-4" fill="none" stroke="#4a90d9"/></svg>Email address</div>
  <div class="login-input" style="top:421px"><svg width="10" height="12" viewBox="0 0 10 12"><rect x="1" y="5" width="8" height="6.5" fill="#4a90d9"/><path d="M2.8 5V3.3a2.2 2.2 0 0 1 4.4 0V5" fill="none" stroke="#4a90d9" stroke-width="1.2"/></svg>Password</div>
  <div class="btn primary" style="left:9px;width:280px;top:482px">Sign up with Email address</div>
</section>

<section class="screen form" style="left:318px;top:664px;height:528px">
  <div class="status" style="background:#fff">⏰ ▾◢ ▯ 16:54</div>
  <div class="topbar" style="height:38px;border:none">
    <h1 style="top:13px;left:9px">Register Your Business</h1>
    <svg class="abs" style="right:10px;top:13px" width="12" height="12" viewBox="0 0 12 12"><path d="M1 1l10 10M11 1L1 11" stroke="#333" stroke-width="1.6"/></svg>
  </div>
  <div class="progress"><i style="width:90%"></i></div>
  <h3>Contact Details (1/2)</h3>
  <div class="label" style="left:8px;top:125px">YOUR WEBSITE URL</div>
  <div class="field" style="left:8px;width:280px;top:140px">www.verdalink-demo.com</div>
  <div class="label" style="left:8px;top:187px">YOUR PHONE NUMBER</div>
  <div class="field" style="left:8px;width:280px;top:202px">01000 555 672</div>
  <div class="label" style="left:8px;top:248px">CITY</div>
  <div class="field" style="left:8px;width:280px;top:263px">New York</div>
  <div class="label" style="left:8px;top:323px">SOCIAL MEDIA</div>
  <div class="btn social-a" style="left:8px;width:280px;top:339px"><i class="sq"></i>Connect Socialine</div>
  <div class="btn social-b" style="left:8px;width:280px;top:382px"><i class="ring"></i>Connect Chirper</div>
  <div class="btn primary" style="left:8px;width:280px;top:482px"><svg width="12" height="12" viewBox="0 0 12 12"><circle cx="6" cy="6" r="5.3" fill="none" stroke="#fff"/><path d="M3.5 6l1.8 1.8L8.7 4.3" fill="none" stroke="#fff" stroke-width="1.2"/></svg>Register</div>
</section>

<section class="screen form" style="left:626px;top:664px;height:528px">
  <div class="status" style="background:#fff">⏰ ▾◢ ▯ 16:54</div>
  <div class="topbar" style="height:38px;border:none">
    <h1 style="top:13px;left:9px">Register Your Business</h1>
    <svg class="abs" style="right:10px;top:13px" width="12" height="12" viewBox="0 0 12 12"><path d="M1 1l10 10M11 1L1 11" stroke="#333" stroke-width="1.6"/></svg>
  </div>
  <div class="progress"><i style="width:64%"></i></div>
  <h3>About You (1/2)</h3>
  <div class="label" style="left:8px;top:125px">BUSINESS NAME</div>
  <div class="field" style="left:8px;width:280px;top:140px">Verdalink Inc.</div>
  <div class="label" style="left:8px;top:187px">ADDRESS</div>
  <div class="field" style="left:8px;width:280px;top:202px">48 Orchard Lane</div>
  <div class="label" style="left:8px;top:248px">CITY</div>
  <div class="field" style="left:8px;width:280px;top:263px">New York</div>
  <div class="label" style="left:8px;top:312px">STATE</div>
  <div class="field" style="left:8px;width:136px;top:326px;font-weight:600;justify-content:space-between">New York <svg width="8" height="5" viewBox="0 0 8 5"><path d="M1 1l3 3 3-3" fill="none" stroke="#333"/></svg></div>
  <div class="label" style="left:152px;top:312px">ZIP CODE</div>
  <div class="field" style="left:152px;width:136px;top:326px">10999</div>
  <div class="btn primary" style="left:8px;width:280px;top:482px">Next <svg width="11" height="9" viewBox="0 0 11 9"><path d="M0 4.5h10M6 .5l4 4-4 4" fill="none" stroke="#fff" stroke-width="1.3"/></svg></div>
</section>

</body>
</html>
```